Design eines Zertifikats
Ich bin total begeistert. Super Kommunikation, super schnelle Reaktion auf kleine Änderungswünsche, ich bin wirklich rundum zufrieden!! Auch bei weiterführenden Fragen die gar nicht direkt mit dem Design zusammenhingen wurde mir total schnell und sympathisch geholfen, ich kann die Designerin nur wärmstens weiterempfehlen!
Zielgruppe
Ich betreibe einen Onlineshop, in dem ich sogenannte Sterntaufen verkaufe. Ein Kunde bekommt dabei im Zuge seines Kaufes ein Zertifikat ausgestellt mit Daten zu seinem getauften Stern. Es geht hier um das Design eines neuen Zertifikats um möglichst noch mehr Käufer anzusprechen. Es sind bereits 3 Designs vorhanden, das neue sollte sich entsprechend etwas absetzen.
Ich lasse die Zertifikate in einer Druckerei drucken, und bedrucke diese dann selber mit den Daten der Sterntaufe, es muss auf dem Zertifikat also ein heller Bereich vorhanden sein in dem ich drucken kann.
Aufgabenstellung
Das Zertifikat soll A4 sein. Es sollte modern sein und sich wie gesagt möglichst von den bestehenden absetzen, und ein möglichst breites Publikum ansprechen.
Beispiele für Zertifikate der Konkurrenz finden sich unter:
himmelspunkt17.de
nebelverzeichnis.de
lichtpate-bundesweit.de
Das von himmelspunkt17.de gefällt mir persönlich ganz gut, aber lasst euch nicht von den Vorschlägen einschränken.
Bitte nicht zu exzessiv kostenpflichtiges Stockmaterial verwenden, ich mache leider aktuell noch Miese mit dem Shop :-)
Bitte schaut auf meine Webseite um ein Gefühl dafür zu bekommen wie viel Platz für Text vorhanden sein muss.

```html
<!DOCTYPE html>
<html lang="de">
<head>
<meta charset="utf-8">
<title>Sternurkunde</title>
<link rel="stylesheet" href="https://fonts.googleapis.com/css2?family=Ubuntu:wght@400;500;700&display=swap">
<style>
  :root {
    --sky-deep: #0b1a33;
    --sky-mid: #1d3f6e;
    --sky-glow: #2f5f94;
    --gold-light: #f2dc8e;
    --gold-mid: #c9a24a;
    --gold-dark: #9a7328;
    --paper: #f1f1f1;
    --paper-shade: #dcdcdc;
    --seal-navy: #262a6b;
    --seal-white: #ffffff;
    --ink: #111111;
  }
  html, body {
    margin: 0;
    padding: 0;
    overflow: hidden;
    background: #ffffff;
  }
  .certificate {
    position: relative;
    width: 1200px;
    height: 849px;
    overflow: hidden;
    font-family: "Ubuntu", sans-serif;
    color: var(--ink);
  }
  .certificate__backdrop {
    position: absolute;
    inset: 0;
    width: 1200px;
    height: 849px;
  }
  .certificate__content {
    position: absolute;
    left: 577px;
    width: 400px;
    top: 0;
    text-align: center;
    font-size: 18.5px;
    line-height: 1.4;
  }
  .certificate__title {
    position: absolute;
    top: 80px;
    left: 0;
    width: 400px;
    margin: 0;
    font-size: 62px;
    font-weight: 500;
    letter-spacing: 0.5px;
  }
  .certificate__line {
    position: absolute;
    left: 0;
    width: 400px;
    margin: 0;
  }
  .star-data {
    position: absolute;
    left: 69px;
    top: 258px;
    border-collapse: collapse;
    text-align: left;
    font-size: 18.5px;
  }
  .star-data th,
  .star-data td {
    padding: 0;
    height: 25.5px;
    font-weight: 400;
  }
  .star-data th { width: 118px; }
  .star-name {
    position: absolute;
    top: 488px;
    left: 0;
    width: 400px;
    margin: 0;
    font-size: 31px;
    font-weight: 700;
  }
  .register {
    position: absolute;
    left: 617px;
    top: 652px;
    font-size: 18.5px;
    line-height: 26px;
    margin: 0;
  }
</style>
</head>
<body>
<main class="certificate">
  <svg class="certificate__backdrop" viewBox="0 0 1200 849" aria-hidden="false">
    <defs>
      <radialGradient id="skyGradient" cx="0.35" cy="0.45" r="0.8">
        <stop offset="0" stop-color="var(--sky-glow)"/>
        <stop offset="0.5" stop-color="var(--sky-mid)"/>
        <stop offset="1" stop-color="var(--sky-deep)"/>
      </radialGradient>
      <linearGradient id="goldGradient" x1="0" y1="0" x2="1" y2="1">
        <stop offset="0" stop-color="var(--gold-light)"/>
        <stop offset="0.35" stop-color="var(--gold-mid)"/>
        <stop offset="0.6" stop-color="var(--gold-dark)"/>
        <stop offset="0.85" stop-color="var(--gold-light)"/>
        <stop offset="1" stop-color="var(--gold-mid)"/>
      </linearGradient>
      <linearGradient id="paperGradient" x1="0" y1="0" x2="1" y2="1">
        <stop offset="0" stop-color="#f6f6f6"/>
        <stop offset="0.6" stop-color="var(--paper)"/>
        <stop offset="1" stop-color="var(--paper-shade)"/>
      </linearGradient>
    </defs>
    <rect class="night-sky" x="0" y="0" width="700" height="849" fill="url(#skyGradient)" role="img" aria-label="Foto eines Sternenhimmels mit Milchstraße"/>
    <path class="gold-band" d="M420,0 C333,200 333,650 430,849 L1200,849 L1200,0 Z" fill="url(#goldGradient)"/>
    <path class="print-area" d="M555,0 C315,200 315,650 555,849 L1200,849 L1200,0 Z" fill="url(#paperGradient)"/>
    <g class="seal">
      <circle cx="349" cy="423" r="76" fill="var(--seal-white)"/>
      <circle cx="349" cy="423" r="66" fill="none" stroke="var(--seal-navy)" stroke-width="10"/>
      <circle cx="349" cy="423" r="50" fill="var(--seal-navy)"/>
    </g>
  </svg>

  <section class="certificate__content">
    <h1 class="certificate__title">Sternurkunde</h1>
    <p class="certificate__line" style="top:211px">Der Stern mit den Koordinaten</p>
    <table class="star-data">
      <tr><th>RA</th><td>: 15h 17m 31,2s</td></tr>
      <tr><th>HIP Nr.</th><td>: 11753</td></tr>
      <tr><th>DEC</th><td>: 31° 17m 31.6s</td></tr>
      <tr><th>Helligkeit</th><td>: 3,7</td></tr>
    </table>
    <p class="certificate__line" style="top:379px">wurde am 04.03.2020 in das<br>Sterntaufenregister eingetragen.</p>
    <p class="certificate__line" style="top:453px">Der Stern erhält den Namen</p>
    <p class="star-name">Annelie</p>
    <p class="certificate__line" style="top:550px">Freunde sind wie Sterne,<br>sie leuchten uns in der Dunkelheit<br>und wärmen uns den Tag.</p>
  </section>

  <p class="register">Registernummer: 12345-1234-1234<br>Unterschrift:</p>
</main>
</body>
</html>
```